Boutique custom software development company needs new business card

Our nearly 20 year old custom software development company would like to better include the fact that we are now providing Bitcoin services. These new services are B2B include education (how to acquire and securely hold Bitcoin) and integrating Bitcoin payments into existing ecommerce sites or other existing systems. Please keep the card clean and simple. Attached is our current design and some other files. vextorial.com

Target Market(s)

businesses owners interested in long term relationship

Industry/Entity Type

Custom software development and Bitcoin

Contact Information for Business Card

Dale Parker, dale@vextorial.com, vextorial.com, (888) 555-VXTRL

Font styles to use
Other font styles liked:
• monospace

Requirements
Must have
• double-sided
Nice to have
• clean and simple
Should not have
• physical address

```html
<!DOCTYPE html>
<html lang="en">
<head>
<meta charset="utf-8">
<title>Vextorial Business Card</title>
<link rel="stylesheet" href="https://fonts.googleapis.com/css2?family=Poppins:wght@400;700;800&family=Asap+Condensed:wght@400&display=swap">
<style>
  :root {
    --brand-blue: #3e71b7;
    --brand-orange: #f07a23;
    --coin-orange: #f39321;
    --ink: #3a3a3a;
    --rule: #8a8a8a;
    --paper: #ffffff;
    --backdrop: #e5e5e5;
  }
  * { margin: 0; padding: 0; box-sizing: border-box; }
  html, body {
    width: 1200px; height: 1200px; overflow: hidden;
    background: var(--backdrop);
    font-family: "Poppins", sans-serif;
  }
  .canvas { position: relative; width: 1200px; height: 1200px; }

  .card {
    position: absolute;
    width: 592px; height: 366px;
  }
  .card-front {
    left: 120px; top: 215px;
    background: var(--brand-blue);
  }
  .card-back {
    left: 452px; top: 632px;
    background: var(--paper);
  }

  .front-wordmark {
    position: absolute;
    left: 155px; top: 252px;
    width: 290px;
    color: var(--paper);
    font-weight: 800;
    font-size: 50px;
    line-height: 1;
    letter-spacing: -1px;
    text-align: center;
  }

  .back-content {
    position: absolute; inset: 0;
    text-align: center;
  }
  .back-wordmark {
    position: absolute; left: 0; right: 0; top: 42px;
    color: var(--brand-blue);
    font-weight: 800;
    font-size: 52px;
    line-height: 1;
    letter-spacing: -1px;
  }
  .tagline {
    position: absolute; left: 0; right: 0; top: 103px;
    color: var(--brand-blue);
    font-family: "Asap Condensed", sans-serif;
    font-size: 21px;
    letter-spacing: -0.6px;
  }
  .person-name {
    position: absolute; left: 0; right: 0; top: 158px;
    color: var(--brand-orange);
    font-weight: 700;
    font-size: 26px;
    line-height: 1.2;
    letter-spacing: -0.3px;
  }
  .contact-icons {
    position: absolute; left: 200px; top: 212px;
    width: 191px; height: 26px;
    display: flex; align-items: center; justify-content: center; gap: 4px;
  }
  .contact-icons .rule {
    flex: 1; height: 1px; background: var(--rule);
  }
  .contact-icons .rule:first-child { margin-right: 2px; }
  .contact-icons .rule:last-child { margin-left: 2px; }
  .icon-box {
    width: 25px; height: 25px; border-radius: 3px;
    background: var(--brand-blue);
    display: flex; align-items: center; justify-content: center;
  }
  .contact-list {
    position: absolute; left: 0; right: 0; top: 250px;
    list-style: none;
    color: var(--ink);
    font-size: 17px;
    line-height: 25px;
  }
  .contact-list .web-name { color: var(--brand-blue); }

  .service-coin {
    position: absolute;
    left: 476px; top: 256px;
    width: 68px; height: 68px; border-radius: 50%;
    background: var(--coin-orange);
  }
</style>
</head>
<body>
<main class="canvas">

  <section class="card card-front" aria-label="Card front">
    <div class="front-wordmark">VEXTORIAL</div>
  </section>

  <section class="card card-back" aria-label="Card back">
    <div class="back-content">
      <div class="back-wordmark">VEXTORIAL</div>
      <p class="tagline">developer of custom applications</p>
      <h1 class="person-name">DALE PARKER</h1>

      <div class="contact-icons">
        <span class="rule"></span>
        <span class="icon-box" aria-label="Phone">
          <svg width="15" height="13" viewBox="0 0 15 13">
            <path d="M1 4 Q7.5 -1 14 4 L12 6 L10 4.5 L10 3.5 Q7.5 2.5 5 3.5 L5 4.5 L3 6 Z" fill="#fff"/>
            <rect x="3" y="6" width="9" height="6" rx="1" fill="#fff"/>
          </svg>
        </span>
        <span class="icon-box" aria-label="Email">
          <svg width="15" height="11" viewBox="0 0 15 11">
            <rect x="0.7" y="0.7" width="13.6" height="9.6" fill="none" stroke="#fff" stroke-width="1.2"/>
            <path d="M0.7 0.7 L7.5 6 L14.3 0.7 M0.7 10.3 L5.5 4.5 M14.3 10.3 L9.5 4.5" fill="none" stroke="#fff" stroke-width="1"/>
          </svg>
        </span>
        <span class="icon-box" aria-label="Website">
          <svg width="15" height="15" viewBox="0 0 15 15">
            <circle cx="7.5" cy="7.5" r="6.5" fill="#fff"/>
            <path d="M4 4 Q6 3 7 5 Q6 7 4.5 6.5 Z M8.5 8 Q11 8 10.5 11 Q9 12 8.5 10 Z" fill="#3e71b7"/>
          </svg>
        </span>
        <span class="rule"></span>
      </div>

      <ul class="contact-list">
        <li>(888) 555-VXTRL</li>
        <li>dale@vextorial.com</li>
        <li><span class="web-name">vextorial</span>.com</li>
      </ul>
    </div>
    <div class="service-coin" aria-hidden="true"></div>
  </section>

</main>
</body>
</html>
```